Accountability Project Graphics

I want to create 10 social media graphics (new Instagram size 4:5 (1080 x 1350 pixels) focusing on our Quilvo Accountability App, using any of the 3 pictures attached. Use the attached pics only, NO RANDOM STOCK PHOTOGRAPHY. For the color scheme, use the landing page colors/fonts (attached).
You can add any of the 3 photos attached but I mainly need BOLD text that includes these headlines and sub-headlines on them.
Please NOTE for all the headlines below, also add this sub-headline on each graphic:
Stay Consistent with RT in Your Pocket!
Here are the headlines:
• Stop Starting Over Every Monday
• You don't need more willpower. You need more support
• Built for women who are tired of doing this alone
• When Motivation Fades, RT Checks In
• The Support System You've Been Missing
• Support When Motivation Disappears
• What if RT Checked in Every Day?
• The Missing Piece Isn't Another Diet
• Eat the food you love. Stay accountable every day.
• One Bad Meal Doesn't Mean You Failed
women over 40 trying to lose weight

```html
<!DOCTYPE html>
<html lang="en">
<head>
<meta charset="utf-8">
<title>Accountability Project Graphics</title>
<link rel="stylesheet" href="https://fonts.googleapis.com/css2?family=Playfair+Display:ital,wght@0,700;1,700&family=Poppins:wght@600&display=swap">
<style>
  :root {
    --backdrop: #A8284F;
    --plum: #2E1B40;
    --rose: #E25383;
    --blush: #F9C7DE;
    --white: #FFFFFF;
  }
  html, body { margin: 0; padding: 0; }
  body {
    width: 1200px; height: 2957px; overflow: hidden;
    background: var(--backdrop);
  }
  .canvas { position: relative; width: 1200px; height: 2957px; }
  .post {
    position: absolute; width: 431px; height: 538px;
    background: var(--white); overflow: hidden;
  }
  .post svg { display: block; width: 100%; height: 100%; }
  .col-left { left: 158px; }
  .col-right { left: 610px; }
  .row-1 { top: 86px; } .row-2 { top: 647px; } .row-3 { top: 1209px; }
  .row-4 { top: 1770px; } .row-5 { top: 2332px; }
  .plum { fill: var(--plum); } .rose { fill: var(--rose); }
  .blush { fill: var(--blush); } .white { fill: var(--white); }
  .photo { fill: url(#photoTone); }
  .headline { font-family: 'Playfair Display', serif; font-weight: 700; fill: var(--white); }
  .headline .accent { fill: var(--rose); }
  .headline .italic { font-style: italic; }
  .subline { font-family: 'Poppins', sans-serif; font-weight: 600; font-size: 16px; fill: var(--white); }
  .subline .accent { fill: var(--rose); }
</style>
</head>
<body>
<svg width="0" height="0" style="position:absolute" aria-hidden="true">
  <defs>
    <linearGradient id="photoTone" x1="0" y1="0" x2="0.4" y2="1">
      <stop offset="0" stop-color="#E9DCCD"/>
      <stop offset="0.55" stop-color="#A89184"/>
      <stop offset="1" stop-color="#4A3D4A"/>
    </linearGradient>
  </defs>
</svg>
<main class="canvas">

  <!-- Post 1 -->
  <section class="post col-left row-1">
    <svg viewBox="0 0 375 469">
      <circle class="blush" cx="50" cy="60" r="150"/>
      <g role="img" aria-label="Photo of two smiling women standing together"><circle class="photo" cx="280" cy="105" r="125"/></g>
      <circle class="plum" cx="375" cy="255" r="70"/>
      <circle class="plum" cx="145" cy="375" r="150"/>
      <rect class="plum" x="0" y="375" width="150" height="94"/>
      <circle class="plum" cx="44" cy="68" r="24"/>
      <circle class="rose" cx="58" cy="133" r="11"/>
      <circle class="rose" cx="329" cy="380" r="24"/>
      <circle class="rose" cx="343" cy="442" r="11"/>
      <text class="headline" font-size="33" x="22">
        <tspan class="accent" y="287">Stop Starting</tspan>
        <tspan x="22" y="325">Over Every</tspan>
        <tspan class="italic" x="22" y="363">Monday</tspan>
      </text>
      <text class="subline" x="20"><tspan class="accent" y="402">Stay Consistent with</tspan><tspan x="20" y="424">RT in Your Pocket!</tspan></text>
    </svg>
  </section>

  <!-- Post 2 -->
  <section class="post col-right row-1">
    <svg viewBox="0 0 375 469">
      <circle class="blush" cx="20" cy="440" r="120"/>
      <circle class="plum" cx="55" cy="55" r="235"/>
      <g role="img" aria-label="Photo of a smiling woman in a black top"><circle class="photo" cx="260" cy="310" r="132"/></g>
      <circle class="plum" cx="327" cy="62" r="20"/>
      <circle class="rose" cx="335" cy="123" r="9"/>
      <circle class="rose" cx="62" cy="343" r="24"/>
      <circle class="rose" cx="76" cy="428" r="11"/>
      <circle class="plum" cx="138" cy="430" r="5"/>
      <text class="headline" font-size="30" x="24">
        <tspan y="48">You don't need</tspan>
        <tspan x="24" y="83">more willpower.</tspan>
        <tspan class="italic" x="24" y="118">You need more</tspan>
        <tspan class="italic" x="24" y="153">support</tspan>
      </text>
      <text class="subline" x="24"><tspan class="accent" y="185">Stay Consistent</tspan><tspan x="24" y="206"><tspan class="accent">with</tspan> RT in Your</tspan><tspan x="24" y="227">Pocket!</tspan></text>
    </svg>
  </section>

  <!-- Post 3 -->
  <section class="post col-left row-2">
    <svg viewBox="0 0 375 469">
      <circle class="blush" cx="370" cy="440" r="135"/>
      <g role="img" aria-label="Photo of two women sharing a joyful hug"><circle class="photo" cx="255" cy="120" r="125"/></g>
      <circle class="plum" cx="115" cy="300" r="150"/>
      <rect class="plum" x="0" y="110" width="115" height="359"/>
      <rect class="plum" x="0" y="300" width="140" height="169"/>
      <circle class="rose" cx="130" cy="47" r="24"/>
      <circle class="rose" cx="48" cy="84" r="11"/>
      <circle class="plum" cx="322" cy="385" r="19"/>
      <circle class="rose" cx="295" cy="439" r="9"/>
      <text class="headline" font-size="32" x="22">
        <tspan y="166">Built</tspan><tspan x="22" y="204">for</tspan><tspan x="22" y="242">women</tspan>
        <tspan x="22" y="280">who are tired</tspan><tspan x="22" y="318">of doing this</tspan><tspan x="22" y="356">alone</tspan>
      </text>
      <text class="subline" x="20"><tspan class="accent" y="390">Stay Consistent with</tspan><tspan x="20" y="412">RT in Your Pocket!</tspan></text>
    </svg>
  </section>

  <!-- Post 4 -->
  <section class="post col-right row-2">
    <svg viewBox="0 0 375 469">
      <circle class="plum" cx="189" cy="356" r="175"/>
      <circle class="white" cx="189" cy="116" r="130"/>
      <g role="img" aria-label="Photo of a smiling woman in a black top"><circle class="photo" cx="189" cy="116" r="122"/></g>
      <circle class="plum" cx="49" cy="113" r="24"/>
      <circle class="rose" cx="343" cy="181" r="16"/>
      <circle class="rose" cx="343" cy="223" r="8"/>
      <circle class="rose" cx="44" cy="215" r="9"/>
      <text class="headline" font-size="34" text-anchor="middle">
        <tspan x="189" y="282">When</tspan>
        <tspan x="189" y="326">Motivation Fades,</tspan>
        <tspan class="italic" x="189" y="371">RT Checks In</tspan>
      </text>
      <text class="subline" text-anchor="middle"><tspan class="accent" x="189" y="403">Stay Consistent</tspan><tspan x="189" y="424"><tspan class="accent">with</tspan> RT in Your Pocket!</tspan></text>
    </svg>
  </section>

  <!-- Post 5 -->
  <section class="post col-left row-3">
    <svg viewBox="0 0 375 469">
      <circle class="blush" cx="30" cy="30" r="100"/>
      <circle class="blush" cx="380" cy="469" r="80"/>
      <circle class="plum" cx="335" cy="125" r="212"/>
      <g role="img" aria-label="Photo of two smiling women standing together"><circle class="photo" cx="115" cy="340" r="130"/></g>
      <circle class="plum" cx="54" cy="99" r="20"/>
      <circle class="rose" cx="76" cy="155" r="9"/>
      <circle class="rose" cx="335" cy="327" r="24"/>
      <circle class="plum" cx="275" cy="384" r="12"/>
      <circle class="rose" cx="315" cy="437" r="8"/>
      <text class="headline" font-size="31" x="150">
        <tspan y="84">The Support</tspan><tspan x="150" y="122">System You've</tspan><tspan x="150" y="160">Been Missing</tspan>
      </text>
      <text class="subline" x="221"><tspan class="accent" y="200">Stay Consistent</tspan><tspan x="221" y="220"><tspan class="accent">with</tspan> RT in Your</tspan><tspan x="221" y="240">Pocket!</tspan></text>
    </svg>
  </section>

  <!-- Post 6 -->
  <section class="post col-right row-3">
    <svg viewBox="0 0 375 469">
      <circle class="plum" cx="0" cy="237" r="60"/>
      <g role="img" aria-label="Photo of two women sharing a joyful hug"><circle class="photo" cx="134" cy="107" r="135"/></g>
      <circle class="plum" cx="250" cy="390" r="180"/>
      <rect class="plum" x="250" y="390" width="125" height="79"/>
      <circle class="rose" cx="322" cy="110" r="24"/>
      <circle class="rose" cx="300" cy="169" r="11"/>
      <circle class="rose" cx="49" cy="235" r="11"/>
      <circle class="rose" cx="49" cy="407" r="24"/>
      <text class="headline" x="122">
        <tspan font-size="30" y="294">Support When</tspan>
        <tspan font-size="40" x="122" y="337">Motivation</tspan>
        <tspan font-size="32" x="122" y="374">Disappears</tspan>
      </text>
      <text class="subline" x="120"><tspan class="accent" y="412">Stay Consistent with</tspan><tspan x="120" y="434">RT in Your Pocket!</tspan></text>
    </svg>
  </section>

  <!-- Post 7 -->
  <section class="post col-left row-4">
    <svg viewBox="0 0 375 469">
      <circle class="blush" cx="170" cy="200" r="125"/>
      <circle class="plum" cx="0" cy="138" r="95"/>
      <g role="img" aria-label="Photo of a smiling woman in a black top"><circle class="photo" cx="257" cy="130" r="132"/></g>
      <circle class="plum" cx="130" cy="400" r="165"/>
      <circle class="rose" cx="67" cy="78" r="24"/>
      <circle class="plum" cx="119" cy="36" r="6"/>
      <circle class="rose" cx="121" cy="195" r="11"/>
      <circle class="plum" cx="333" cy="363" r="20"/>
      <circle class="rose" cx="334" cy="433" r="9"/>
      <text class="headline" font-size="34" x="50">
        <tspan y="310">What if RT</tspan><tspan x="50" y="351">Checked in</tspan><tspan x="50" y="391">Every Day?</tspan>
      </text>
      <text class="subline" x="48"><tspan class="accent" y="422">Stay Consistent with</tspan><tspan x="48" y="444">RT in Your Pocket!</tspan></text>
    </svg>
  </section>

  <!-- Post 8 -->
  <section class="post col-right row-4">
    <svg viewBox="0 0 375 469">
      <circle class="blush" cx="385" cy="258" r="105"/>
      <circle class="blush" cx="0" cy="60" r="60"/>
      <circle class="plum" cx="189" cy="113" r="170"/>
      <g role="img" aria-label="Photo of two smiling women standing together"><circle class="photo" cx="187" cy="388" r="150"/></g>
      <circle class="rose" cx="64" cy="261" r="10"/>
      <circle class="plum" cx="340" cy="384" r="19"/>
      <text class="headline" font-size="34" text-anchor="middle">
        <tspan x="189" y="54">The</tspan><tspan x="189" y="98">Missing Piece</tspan><tspan x="189" y="143">Isn't Another Diet</tspan>
      </text>
      <text class="subline" text-anchor="middle"><tspan class="accent" x="189" y="182">Stay Consistent</tspan><tspan x="189" y="203"><tspan class="accent">with</tspan> RT in Your Pocket!</tspan></text>
    </svg>
  </section>

  <!-- Post 9 -->
  <section class="post col-left row-5">
    <svg viewBox="0 0 375 469">
      <circle class="plum" cx="270" cy="90" r="180"/>
      <circle class="plum" cx="125" cy="305" r="150"/>
      <g role="img" aria-label="Photo of two women sharing a joyful hug"><circle class="photo" cx="137" cy="329" r="140"/></g>
      <circle class="plum" cx="44" cy="57" r="20"/>
      <circle class="rose" cx="91" cy="112" r="9"/>
      <circle class="rose" cx="337" cy="254" r="24"/>
      <text class="headline" font-size="28" x="143">
        <tspan class="italic" y="42">Eat the food</tspan><tspan class="italic" x="143" y="75">you love.</tspan>
        <tspan x="143" y="110">Stay accountable</tspan><tspan x="143" y="143">every day.</tspan>
      </text>
      <text class="subline" x="221"><tspan class="accent" y="183">Stay Consistent</tspan><tspan x="221" y="203"><tspan class="accent">with</tspan> RT in Your</tspan><tspan x="221" y="223">Pocket!</tspan></text>
    </svg>
  </section>

  <!-- Post 10 -->
  <section class="post col-right row-5">
    <svg viewBox="0 0 375 469">
      <circle class="blush" cx="380" cy="0" r="85"/>
      <circle class="blush" cx="0" cy="469" r="100"/>
      <circle class="plum" cx="239" cy="0" r="90"/>
      <g role="img" aria-label="Photo of a smiling woman in a black top"><circle class="photo" cx="70" cy="200" r="150"/></g>
      <circle class="plum" cx="269" cy="289" r="175"/>
      <circle class="rose" cx="296" cy="59" r="20"/>
      <circle class="rose" cx="233" cy="107" r="9"/>
      <circle class="plum" cx="65" cy="394" r="24"/>
      <text class="headline" font-size="34" text-anchor="middle">
        <tspan class="accent" x="269" y="165">One</tspan><tspan class="accent" x="269" y="204">Bad Meal</tspan>
        <tspan x="269" y="242">Doesn't</tspan><tspan x="269" y="281">Mean You</tspan><tspan x="269" y="319">Failed</tspan>
      </text>
      <text class="subline" text-anchor="middle"><tspan class="accent" x="269" y="352">Stay Consistent</tspan><tspan x="269" y="373"><tspan class="accent">with</tspan> RT in Your</tspan><tspan x="269" y="394">Pocket!</tspan></text>
    </svg>
  </section>

</main>
</body>
</html>
```